Visitenkarte für Ergotherapiepraxis
Zielgruppe
Wir arbeiten mit Kindern und Erwachsene jeden Alters.
Diese Personen kommen mit Beeinträchtigungen (körperlich, seelisch, schulisch) im täglichen Leben zu uns. Wir unterstützen unsere Patienten die Beeinträchtigungen zu verringern oder zu kompensieren und so den Alltag besser bewältigen zu können.
Aufgabenstellung
Ein Design was Kinder und Erwachsene anspricht, aber nicht zu verspielt wirkt. Es soll vertrauenserweckend sein. Eventuell sollte die Visitenkarte ein "aufgehendes oder erblühendes oder aufsteigendes" Element enthalten (=zu Beginn war die Beeinträchtigung dann steigt die Lebensqualität als Folge der Behandlung)
Daten vorn:
Ergotherapiepraxis

```html
<!DOCTYPE html>
<html lang="de">
<head>
<meta charset="utf-8">
<title>Visitenkarte Ergotherapiepraxis</title>
<link rel="stylesheet" href="https://fonts.googleapis.com/css2?family=Allura&family=Roboto+Condensed:wght@300&display=swap">
<style>
  :root {
    --bg: #eeeeee;
    --card: #ffffff;
    --ink: #2b2b2b;
    --ink-soft: #6b6b6b;
    --bloom-teal: #5fcbe0;
    --bloom-blue: #3a8fd6;
    --bloom-violet: #8a6cc4;
    --bloom-lilac: #c9b6e6;
    --bloom-mint: #8fd8c8;
  }
  * { margin: 0; padding: 0; box-sizing: border-box; }
  html, body { width: 1200px; height: 847px; overflow: hidden; }
  body { background: var(--bg); position: relative; }

  .card {
    position: absolute;
    top: 238px;
    width: 486px;
    height: 319px;
    background: var(--card);
    box-shadow: 0 3px 8px rgba(0,0,0,0.18);
    overflow: hidden;
  }
  .card--front { left: 111px; }
  .card--back { left: 615px; }

  .bloom { position: absolute; inset: 0; width: 100%; height: 100%; }

  .card__name {
    position: absolute;
    font-family: "Allura", cursive;
    font-size: 46px;
    line-height: 1;
    color: var(--ink);
  }
  .card__label,
  .card__address {
    position: absolute;
    font-family: "Roboto Condensed", sans-serif;
    font-weight: 300;
    color: var(--ink);
    font-size: 19px;
    letter-spacing: 0.04em;
    line-height: 28px;
  }
  .card--front .card__name { left: 24px; top: 30px; }
  .card--front .card__label { left: 26px; top: 74px; letter-spacing: 0.09em; }
  .card--front .card__address { left: 26px; top: 126px; }

  .card--back .card__label { left: 28px; top: 16px; color: var(--ink-soft); }
  .card--back .card__name { left: 24px; top: 60px; }
</style>
</head>
<body>
  <section class="card card--front">
    <svg class="bloom" viewBox="0 0 486 319" role="img" aria-label="Aufblühende Blumenillustration in Türkis, Blau und Violett mit Ranken und Schmetterlingen">
      <defs>
        <radialGradient id="bloom-front" cx="0.85" cy="0.9" r="0.8">
          <stop offset="0" stop-color="var(--bloom-blue)"/>
          <stop offset="0.45" stop-color="var(--bloom-violet)" stop-opacity="0.75"/>
          <stop offset="0.8" stop-color="var(--bloom-teal)" stop-opacity="0.35"/>
          <stop offset="1" stop-color="var(--bloom-mint)" stop-opacity="0"/>
        </radialGradient>
      </defs>
      <path d="M200 319 C230 250 290 210 350 180 C390 150 430 100 486 80 L486 319 Z" fill="url(#bloom-front)"/>
    </svg>
    <p class="card__name">Marlene Sorge</p>
    <p class="card__label">Ergotherapiepraxis</p>
    <p class="card__address">Am Lindenweg 12<br>14943 Luckenwalde, OT Wiesen<br>Tel. 03371/48215</p>
  </section>

  <section class="card card--back">
    <svg class="bloom" viewBox="0 0 486 319" role="img" aria-label="Große aufblühende Blumenillustration in Türkis, Blau und Violett mit Ranken und Schmetterlingen">
      <defs>
        <radialGradient id="bloom-back" cx="0.78" cy="0.45" r="0.75">
          <stop offset="0" stop-color="var(--bloom-teal)"/>
          <stop offset="0.4" stop-color="var(--bloom-blue)" stop-opacity="0.9"/>
          <stop offset="0.75" stop-color="var(--bloom-violet)" stop-opacity="0.6"/>
          <stop offset="1" stop-color="var(--bloom-lilac)" stop-opacity="0"/>
        </radialGradient>
      </defs>
      <path d="M0 319 L0 250 C60 220 120 230 170 200 C200 130 240 40 300 0 L486 0 L486 319 Z" fill="url(#bloom-back)"/>
    </svg>
    <p class="card__label">Behandelnder Therapeut:</p>
    <p class="card__name">Marlene Sorge</p>
  </section>
</body>
</html>
```